Flask Mint Studio needs wedding label designs!

Flask Mint Studio is looking for new wedding designs! Please look at http://www.flaskmintstudio.com/water-bottle-labels and http://www.flaskmintstudio.com/custom-water to get an idea of what we currently offer.

These new designs will be saved onto Flask Mint Studio so that customers can come and customize the text and/or add pictures on them for purchase as water bottle labels or custom label bottled water.

Designs must appeal to a broad audience so any and all styles will be considered. Some other sites to draw inspiration from are plumcards.com, velvora.com, altarinkqueens.com and fernly.com.

Questions? Ask away!

Target Market(s)

Target market is brides, mothers of brides and wedding planners.

Industry/Entity Type

Wedding

Requirements
Must have
• Designs must be at 300 dpi in CMYK. Width is 8.133" Height is 2.377" with a .125" bleed around all sides.

```html
<!DOCTYPE html>
<html lang="en">
<head>
<meta charset="utf-8">
<title>Wedding Water Bottle Labels – Clara &amp; Daniel</title>
<link rel="stylesheet" href="https://fonts.googleapis.com/css2?family=Arimo:wght@400;700&family=Marcellus+SC&display=swap">
<style>
  :root {
    --canvas-bg: #f2f2f2;
    --berry: #a3186a;
    --berry-stripe: #c0478f;
    --cocoa: #5a3a1c;
    --blush: #f7c4b0;
    --berry-text: #a0176a;
    --lagoon: #2b7a93;
    --lagoon-deep: #0f4a60;
    --label-white: #ffffff;
  }

  * { margin: 0; padding: 0; box-sizing: border-box; }

  html, body {
    width: 1200px;
    height: 900px;
    overflow: hidden;
    background: var(--canvas-bg);
  }

  .label-sheet {
    width: 1200px;
    height: 900px;
    display: flex;
    flex-direction: column;
    align-items: center;
    justify-content: center;
    gap: 90px;
  }

  .bottle-label {
    position: relative;
    width: 1000px;
    height: 292px;
    overflow: hidden;
    box-shadow: 0 2px 10px rgba(0, 0, 0, 0.12);
  }

  /* Blush & berry label */
  .label-blush .stripe-band {
    position: absolute;
    left: 0; top: 0;
    width: 100%;
    height: 110px;
    background: linear-gradient(90deg, var(--berry), var(--berry-stripe) 50%, var(--berry));
  }
  .label-blush .cocoa-rule {
    position: absolute;
    left: 0; top: 110px;
    width: 100%;
    height: 16px;
    background: var(--cocoa);
  }
  .label-blush .damask-field {
    position: absolute;
    left: 0; top: 126px;
    width: 100%;
    height: 166px;
    background: var(--blush);
  }
  .label-blush .couple-block {
    position: absolute;
    left: 0; top: 126px;
    width: 100%;
    height: 166px;
    display: flex;
    flex-direction: column;
    align-items: center;
    justify-content: center;
    font-family: "Arimo", Arial, sans-serif;
    color: var(--berry-text);
    font-weight: 700;
  }
  .label-blush .couple-names {
    font-size: 46px;
    letter-spacing: 1px;
    line-height: 1.1;
  }
  .label-blush .wedding-date {
    font-size: 26px;
    margin-top: 6px;
  }

  /* Lagoon & navy label */
  .label-lagoon .floral-field {
    position: absolute;
    inset: 0;
    background: linear-gradient(180deg, #3a8aa3, var(--lagoon) 50%, #23697f);
  }
  .label-lagoon .name-panel {
    position: absolute;
    top: 0;
    left: 50%;
    transform: translateX(-50%);
    width: 400px;
    height: 100%;
    background: var(--lagoon-deep);
    border-left: 12px solid var(--label-white);
    border-right: 12px solid var(--label-white);
    display: flex;
    flex-direction: column;
    align-items: center;
    justify-content: center;
    font-family: "Marcellus SC", "Times New Roman", serif;
    color: var(--label-white);
    text-align: center;
  }
  .label-lagoon .couple-names {
    font-size: 50px;
    line-height: 1.08;
  }
  .label-lagoon .wedding-date {
    font-size: 24px;
    margin-top: 22px;
    letter-spacing: 1px;
  }
</style>
</head>
<body>
  <main class="label-sheet">
    <section class="bottle-label label-blush">
      <div class="stripe-band" role="img" aria-label="Berry pinstripe pattern band"></div>
      <div class="cocoa-rule"></div>
      <div class="damask-field" role="img" aria-label="Soft blush damask pattern background"></div>
      <div class="couple-block">
        <p class="couple-names">CLARA &amp; DANIEL</p>
        <p class="wedding-date">May 15, 2011</p>
      </div>
    </section>

    <section class="bottle-label label-lagoon">
      <div class="floral-field" role="img" aria-label="Teal hibiscus flower pattern background"></div>
      <div class="name-panel">
        <p class="couple-names">Clara<br>&amp;<br>Daniel</p>
        <p class="wedding-date">May 15, 2011</p>
      </div>
    </section>
  </main>
</body>
</html>
```